Business Card and Simple Logo Desgin

New Zealand based start up company "Vesta Advisory LTD" requires business cards and simple logo design.

Card Content.

Vesta Advisory LTD

Rebecca Thornbury
CA, BMS (Hons)

r.thornbury@vestaadvisory.co.nz
PH +64 21 574 613

Target Market(s)

Corporate Business in IT, Finance and accounting.

Industry/Entity Type

Business

```html
<!DOCTYPE html>
<html lang="en">
<head>
<meta charset="utf-8">
<title>Vesta Advisory LTD — Business Card</title>
<link rel="stylesheet" href="https://fonts.googleapis.com/css2?family=Hind:wght@400;500&display=swap">
<style>
  :root {
    --page-bg: #eef0f2;
    --card-bg: #fafbfc;
    --brand-blue: #0a8fca;
    --accent-tint: #c9e0ed;
    --ink: #2b2f33;
    --ink-soft: #55595e;
  }
  html, body {
    margin: 0;
    width: 1200px;
    height: 900px;
    overflow: hidden;
    background: var(--page-bg);
  }
  .canvas {
    position: relative;
    width: 1200px;
    height: 900px;
  }
  .business-card {
    position: absolute;
    left: 170px;
    top: 175px;
    width: 860px;
    height: 550px;
    border-radius: 26px;
    background: var(--card-bg);
    overflow: hidden;
    box-shadow: 0 2px 10px rgba(0, 0, 0, 0.08);
    font-family: "Hind", sans-serif;
  }
  .accent-arc {
    position: absolute;
    left: 0;
    top: 0;
  }
  .brand {
    position: absolute;
    left: 62px;
    top: 300px;
    display: flex;
    align-items: flex-start;
    gap: 18px;
  }
  .brand-dot {
    width: 34px;
    height: 34px;
    border-radius: 50%;
    background: var(--brand-blue);
    margin-top: 6px;
  }
  .brand-name {
    margin: 0;
    color: var(--brand-blue);
    font-weight: 400;
    font-size: 38px;
    line-height: 0.92;
  }
  .contact {
    position: absolute;
    right: 22px;
    top: 345px;
    text-align: right;
    color: var(--ink);
  }
  .contact-name {
    margin: 0;
    font-weight: 500;
    font-size: 27px;
    line-height: 1.1;
  }
  .contact-credentials {
    margin: 2px 0 0;
    font-size: 16px;
    color: var(--ink-soft);
  }
  .contact-email {
    margin: 20px 0 0;
    font-size: 26px;
    line-height: 1.1;
  }
  .contact-phone {
    margin: 8px 0 0;
    font-size: 26px;
    line-height: 1.1;
  }
  .contact-phone .label {
    font-size: 16px;
    margin-right: 8px;
    color: var(--ink-soft);
  }
</style>
</head>
<body>
<main class="canvas">
  <section class="business-card" aria-label="Vesta Advisory business card">
    <svg class="accent-arc" width="860" height="550" viewBox="0 0 860 550" aria-hidden="true">
      <circle cx="647" cy="492" r="292" fill="var(--accent-tint)"/>
    </svg>

    <div class="brand">
      <span class="brand-dot" aria-hidden="true"></span>
      <p class="brand-name">vesta<br>advisory<br>ltd</p>
    </div>

    <div class="contact">
      <p class="contact-name">Rebecca Thornbury</p>
      <p class="contact-credentials">CA, BMS (Hons)</p>
      <p class="contact-email">r.thornbury@vestaadvisory.co.nz</p>
      <p class="contact-phone"><span class="label">Tel</span>+64 21 574 613</p>
    </div>
  </section>
</main>
</body>
</html>
```